New eyelid plastic surgery office needs a business card design-Eyelid Care Partners of the Brenton

I recently used PixelForge for my logo design and was very pleased with creativity and results. It was a difficult decision for me. Now I would like to create a business card based on this logo, which I will attach.

The text should be easily legible as some of my patients have difficulty seeing, but I would like a subtle, sophisticated artistry also evident to make the card memorable. Would like the card based on a similar color scheme as the logo but the inverse or other complementary colors may prove interesting
Updates

A good question was asked...my concern about my visually impaired patients was really my desire to avoid italicized or calligraphic type fonts that may be hard to read. Standard font size for a business card would be fine. Thanks!

Thank you so much for the great work so far. I wanted to give you my particular contact information to see if that would change the look of the cards. Martin Delacourt, MD Address: 2718 Harborview Lane, Suite 206 Brenton Bay, BR 28517 Phone: 010-555-0193 Fax: 010-555-0194 Website: www.brentonlidstudio.example Please delete the email slot from the card. Thanks so much!

Industry/Entity Type

Plastic

```html
<!DOCTYPE html>
<html lang="en">
<head>
<meta charset="utf-8">
<title>Eyelid Care Partners of the Brenton – Business Card</title>
<link rel="stylesheet" href="https://fonts.googleapis.com/css2?family=Arimo:wght@400;700&display=swap">
<style>
  :root {
    --backdrop: #ece9e4;
    --card-white: #ffffff;
    --header-light: #a3a3a3;
    --header-mid: #8a8a8a;
    --header-dark: #4a4a4a;
    --rule-grey: #b5b5b5;
    --brand-blue: #1e58b0;
    --ink: #111111;
  }
  * { box-sizing: border-box; margin: 0; padding: 0; }
  html, body {
    width: 1200px; height: 888px; overflow: hidden;
    background: var(--backdrop);
    font-family: "Arimo", Arial, sans-serif;
  }
  .business-card {
    position: absolute; left: 80px; top: 144px;
    width: 1040px; height: 600px;
    background: var(--card-white);
    box-shadow: 0 6px 18px rgba(0,0,0,0.25);
    overflow: hidden;
  }
  .card-header {
    position: absolute; left: 0; top: 0; width: 100%; height: 280px;
    background: radial-gradient(ellipse at 45% 30%, var(--header-light) 0%, var(--header-mid) 55%, var(--header-dark) 100%);
    display: flex; flex-direction: column; align-items: center; justify-content: center;
    color: var(--brand-blue); font-weight: 700; text-transform: uppercase; text-align: center;
  }
  .brand-name-main { font-size: 64px; letter-spacing: 1px; line-height: 1.05; }
  .brand-name-sub { font-size: 36px; letter-spacing: 1px; line-height: 1.2; margin-top: 6px; }
  .header-band { position: absolute; left: 0; top: 280px; width: 100%; }
  .band-rule { height: 8px; background: var(--rule-grey); }
  .band-blue { height: 22px; background: var(--brand-blue); }
  .contact-block {
    position: absolute; left: 70px; top: 345px; width: 920px;
    border-left: 3px solid var(--ink);
    padding-left: 18px;
    color: var(--ink); font-weight: 700;
  }
  .contact-heading { font-size: 24px; }
  .contact-heading span { margin-left: 22px; }
  .practitioner-name { font-size: 38px; margin: 8px 0 14px 180px; }
  .contact-list { display: grid; grid-template-columns: 112px 1fr; row-gap: 4px; font-size: 24px; }
  .contact-list dt, .contact-list dd { font-weight: 700; white-space: nowrap; }
</style>
</head>
<body>
  <article class="business-card">
    <header class="card-header">
      <div class="brand-name-main">Eyelid Care Partners</div>
      <div class="brand-name-sub">of the Brenton</div>
    </header>
    <div class="header-band">
      <div class="band-rule"></div>
      <div class="band-blue"></div>
      <div class="band-rule"></div>
    </div>
    <section class="contact-block">
      <p class="contact-heading">Contact<span>:</span></p>
      <p class="practitioner-name">Martin Delacourt, MD</p>
      <dl class="contact-list">
        <dt>Address</dt><dd>: 2718 Harborview Lane, Suite 206 Brenton Bay, BR 28517</dd>
        <dt>Phone</dt><dd>: 010 - 555 - 0193</dd>
        <dt>Fax</dt><dd>: 010 - 555 - 0194</dd>
        <dt>web</dt><dd>: www.brentonlidstudio.example</dd>
      </dl>
    </section>
  </article>
</body>
</html>
```